Fern Moss Cleaning Tablets needs 4 x labels

We're about to launch a very exciting cleaning product to market and need your help to brand the 4 x bottles. www.fernmossly.com.au will change the way people buy and use household cleaning products whilst significantly reducing the impact on the earth.

The tablets are dropped into the long life recycled plastic bottle, you simply add water, wait for the tab to dissolve and begin cleaning.

Target Market(s)

Women aged between 30 - 65, care for the environment, want to use less plastic, are early adopters and like to try new things. Care about a clean home and using less chemicals. Want less packaging, less plastic, less carbon emissions.

Industry/Entity Type

House Cleaning

Font styles to use
Sans Serif

Requirements
Must have
• Each label must have an obvious colour differentiator and each label must be identical in it's dimensions and information. Should look uniform when all 4 bottles are aligned in the cupboard. Limited / no images apart from logo.
Nice to have
• Simple, clear, bold, striking. Limited / no pictures. Clean lines with lots of space.
Should not have
• Sparkwell Pane Label must have a strip of blue (hex BAE1FF).
Grime Hauler Kitchen Cleaner must have a strip of colour (FFD6F3)
The Fizzer Bathroom cleaner must have a colour strip hex # FFFFBA
The Allrounder Multip Purpose must have a strip of colour Hex #BAFFC9

```html
<!DOCTYPE html>
<html lang="en">
<head>
<meta charset="utf-8">
<title>Fern Moss Cleaning Tablets – Bottle Labels</title>
<link rel="stylesheet" href="https://fonts.googleapis.com/css2?family=Bebas+Neue&family=Oswald:wght@500&family=Noto+Serif:ital,wght@1,300&family=Open+Sans:wght@400&display=swap">
<style>
  :root {
    --page: #ffffff;
    --kraft: #cdb793;
    --kraft-deep: #c2aa84;
    --ink: #1f1e1c;
    --window-strip: #b3c9e6;
    --window-text: #6f8fbe;
    --bath-strip: #fbf8c6;
    --bath-text: #dcd18a;
    --kitchen-strip: #f9d9e1;
    --kitchen-text: #d7a3b1;
    --multi-strip: #b4e0cd;
    --multi-text: #76b9a0;
  }
  * { box-sizing: border-box; margin: 0; padding: 0; }
  html, body { width: 1200px; height: 849px; overflow: hidden; background: var(--page); }
  .label-row {
    position: absolute; left: 65px; top: 172px;
    display: flex; gap: 50px;
  }
  .label {
    position: relative; width: 230px; height: 505px; overflow: hidden;
    background: var(--strip);
  }
  .label--window  { --strip: var(--window-strip);  --accent: var(--window-text); }
  .label--bath    { --strip: var(--bath-strip);    --accent: var(--bath-text); }
  .label--kitchen { --strip: var(--kitchen-strip); --accent: var(--kitchen-text); }
  .label--multi   { --strip: var(--multi-strip);   --accent: var(--multi-text); }

  .kraft {
    position: absolute; left: 0; top: 0; width: 100%; height: 272px;
    background: linear-gradient(160deg, var(--kraft), var(--kraft-deep));
  }
  .brand {
    position: absolute; left: 30px; top: 42px;
    display: flex; align-items: center; gap: 8px;
    font-family: "Oswald", sans-serif; font-weight: 500;
    font-size: 34px; line-height: 1; color: var(--ink); letter-spacing: 0.5px;
  }
  .brand-dot { width: 14px; height: 14px; border-radius: 50%; background: var(--ink); }
  .stamp { position: absolute; right: 2px; top: 118px; width: 80px; height: 80px; }
  .stamp circle { fill: none; stroke: var(--accent); stroke-width: 1.3; opacity: 0.75; }

  .category {
    position: absolute; left: 18px; top: 213px;
    font-family: "Noto Serif", serif; font-style: italic; font-weight: 300;
    font-size: 16px; color: var(--accent); white-space: nowrap;
  }
  .product-name {
    position: absolute; left: 16px; top: 242px; right: 12px;
    font-family: "Bebas Neue", sans-serif; font-size: 48px; line-height: 44px;
    color: var(--ink); letter-spacing: 0;
    white-space: nowrap;
  }
  .tagline {
    position: absolute; left: 18px; top: 366px; list-style: none;
    font-family: "Noto Serif", serif; font-style: italic; font-weight: 300;
    font-size: 17px; line-height: 25px; color: var(--accent);
  }
  .volume {
    position: absolute; right: 8px; top: 432px; width: 54px;
    border: 1px solid var(--accent);
    font-family: "Open Sans", sans-serif; text-align: center;
  }
  .volume-place { font-size: 8.5px; line-height: 11px; color: var(--accent); padding-top: 2px; }
  .volume-wave { display: block; width: 28px; height: 6px; margin: 0 auto; }
  .volume-wave path { fill: none; stroke: var(--accent); stroke-width: 1; }
  .volume-size {
    margin-top: 2px; border-top: 1px solid var(--accent);
    font-size: 11.5px; line-height: 17px; color: var(--ink);
  }
</style>
</head>
<body>
<main class="label-row">

  <article class="label label--window">
    <div class="kraft"></div>
    <div class="brand"><span>FERN MOSS</span><span class="brand-dot"></span></div>
    <svg class="stamp" viewBox="0 0 92 92" aria-hidden="true"><circle cx="46" cy="46" r="42"/><circle cx="46" cy="46" r="24"/></svg>
    <p class="category">Window Cleaner</p>
    <h2 class="product-name">Sparkwell<br>Pane</h2>
    <ul class="tagline"><li>One Bottle.</li><li>One Tab.</li><li>Dissolve.</li><li>Clean.</li><li>Repeat.</li></ul>
    <div class="volume">
      <div class="volume-place">Kelpcove</div>
      <svg class="volume-wave" viewBox="0 0 28 6" aria-hidden="true"><path d="M1 4 Q8 0 14 3 T27 2"/></svg>
      <div class="volume-place">Australia</div>
      <div class="volume-size">500 ml</div>
    </div>
  </article>

  <article class="label label--bath">
    <div class="kraft"></div>
    <div class="brand"><span>FERN MOSS</span><span class="brand-dot"></span></div>
    <svg class="stamp" viewBox="0 0 92 92" aria-hidden="true"><circle cx="46" cy="46" r="42"/><circle cx="46" cy="46" r="24"/></svg>
    <p class="category">Bathroom Cleaner</p>
    <h2 class="product-name">The<br>Fizzer</h2>
    <ul class="tagline"><li>One Bottle.</li><li>One Tab.</li><li>Dissolve.</li><li>Clean.</li><li>Repeat.</li></ul>
    <div class="volume">
      <div class="volume-place">Kelpcove</div>
      <svg class="volume-wave" viewBox="0 0 28 6" aria-hidden="true"><path d="M1 4 Q8 0 14 3 T27 2"/></svg>
      <div class="volume-place">Australia</div>
      <div class="volume-size">500 ml</div>
    </div>
  </article>

  <article class="label label--kitchen">
    <div class="kraft"></div>
    <div class="brand"><span>FERN MOSS</span><span class="brand-dot"></span></div>
    <svg class="stamp" viewBox="0 0 92 92" aria-hidden="true"><circle cx="46" cy="46" r="42"/><circle cx="46" cy="46" r="24"/></svg>
    <p class="category">Kitchen Cleaner</p>
    <h2 class="product-name">Grime<br>Hauler</h2>
    <ul class="tagline"><li>One Bottle.</li><li>One Tab.</li><li>Dissolve.</li><li>Clean.</li><li>Repeat.</li></ul>
    <div class="volume">
      <div class="volume-place">Kelpcove</div>
      <svg class="volume-wave" viewBox="0 0 28 6" aria-hidden="true"><path d="M1 4 Q8 0 14 3 T27 2"/></svg>
      <div class="volume-place">Australia</div>
      <div class="volume-size">500 ml</div>
    </div>
  </article>

  <article class="label label--multi">
    <div class="kraft"></div>
    <div class="brand"><span>FERN MOSS</span><span class="brand-dot"></span></div>
    <svg class="stamp" viewBox="0 0 92 92" aria-hidden="true"><circle cx="46" cy="46" r="42"/><circle cx="46" cy="46" r="24"/></svg>
    <p class="category">Multi Purpose Cleaner</p>
    <h2 class="product-name">The<br>Allrounder</h2>
    <ul class="tagline"><li>One Bottle.</li><li>One Tab.</li><li>Dissolve.</li><li>Clean.</li><li>Repeat.</li></ul>
    <div class="volume">
      <div class="volume-place">Kelpcove</div>
      <svg class="volume-wave" viewBox="0 0 28 6" aria-hidden="true"><path d="M1 4 Q8 0 14 3 T27 2"/></svg>
      <div class="volume-place">Australia</div>
      <div class="volume-size">500 ml</div>
    </div>
  </article>

</main>
</body>
</html>
```